Redesign business cards

We have a new logo and I am not that happy with the layout of our existing card and looking for a change. Font is a bit small and the green can be hard to read. Logo may need a tidy up as the copy I have is not that hi-res too so require you to produce a hi-res version of the logo for us too. There will be three individual business cards to produce with just the names and phone numbers being different. Address will change too, but use what you see on the card for now.

Industry/Entity Type

Business

Requirements
Nice to have
• You could consider a redesign to the new logo, just not too radical. We like the blue and green hexagons as we feel that they are representative of oil industry that we are in.

```html
<!DOCTYPE html>
<html lang="en">
<head>
<meta charset="UTF-8">
<title>Hexora Oil Services – Business Cards</title>
<link rel="stylesheet" href="https://fonts.googleapis.com/css2?family=Source+Sans+3:wght@400;600&display=swap">
<style>
  :root {
    --canvas: #ecebe8;
    --leaf-green: #8dc63f;
    --pale-green: #eef6e4;
    --sky-blue: #1da5e2;
    --accent-orange: #f4921f;
    --ink-grey: #5a5a5a;
    --paper: #ffffff;
  }
  * { margin: 0; padding: 0; box-sizing: border-box; }
  html, body { width: 1200px; height: 1200px; overflow: hidden; }
  body {
    background: var(--canvas);
    font-family: "Source Sans 3", Arial, sans-serif;
    display: flex;
    flex-direction: column;
    align-items: center;
    justify-content: center;
    gap: 64px;
  }
  .card {
    position: relative;
    width: 860px;
    height: 492px;
    border-radius: 26px;
    overflow: hidden;
    box-shadow: 0 4px 14px rgba(0,0,0,0.12);
  }
  .card-art { position: absolute; inset: 0; width: 100%; height: 100%; }

  /* Front */
  .brand {
    position: absolute;
    left: 58px;
    top: 82px;
    display: flex;
    align-items: center;
    gap: 18px;
  }
  .brand-mark {
    width: 26px; height: 26px;
    border-radius: 50%;
    background: var(--sky-blue);
  }
  .brand-name {
    font-weight: 600;
    color: var(--leaf-green);
    line-height: 1;
  }
  .brand-name .main { display: block; font-size: 80px; letter-spacing: -1px; }
  .brand-name .sub { display: block; font-size: 32px; margin-top: 4px; }

  .holder {
    position: absolute;
    left: 58px;
    top: 246px;
  }
  .holder-name {
    font-weight: 600;
    font-size: 28px;
    color: var(--accent-orange);
  }
  .holder-role {
    font-size: 18px;
    color: var(--ink-grey);
    margin-top: 6px;
  }

  .contact-list {
    position: absolute;
    left: 592px;
    top: 212px;
    list-style: none;
    color: var(--paper);
    font-size: 20px;
  }
  .contact-list li {
    display: flex;
    align-items: center;
    gap: 10px;
    margin-bottom: 10px;
  }
  .contact-icon { width: 20px; height: 20px; flex: none; }

  .postal {
    position: absolute;
    right: 40px;
    bottom: 34px;
    text-align: right;
    color: var(--paper);
    font-size: 20px;
    line-height: 1.4;
  }

  /* Back */
  .card-back { background: var(--sky-blue); }
  .back-mark {
    position: absolute;
    left: 50%;
    top: 58px;
    transform: translateX(-50%);
    display: flex;
    flex-direction: column;
    align-items: center;
    gap: 26px;
  }
  .back-mark .brand-mark-large {
    width: 170px; height: 170px;
    border-radius: 50%;
    background: var(--paper);
  }
  .back-mark .brand-word {
    font-weight: 600;
    font-size: 46px;
    color: var(--paper);
  }
  .back-url {
    position: absolute;
    left: 0; right: 0;
    bottom: 52px;
    text-align: center;
    color: var(--paper);
    font-size: 24px;
    letter-spacing: 6px;
  }
</style>
</head>
<body>

  <section class="card card-front">
    <svg class="card-art" viewBox="0 0 860 492" preserveAspectRatio="none" aria-hidden="true">
      <rect width="860" height="492" fill="var(--leaf-green)"/>
      <path d="M0 0 H640 C600 200 560 380 0 420 Z" fill="var(--sky-blue)" transform="translate(0 34)"/>
      <path d="M0 0 H640 C600 200 560 380 0 420 Z" fill="var(--pale-green)" transform="translate(0 12)"/>
      <path d="M0 0 H640 C600 200 560 380 0 420 Z" fill="var(--paper)"/>
    </svg>

    <div class="brand">
      <span class="brand-mark"></span>
      <div class="brand-name">
        <span class="main">Hexora</span>
        <span class="sub">Oil Services</span>
      </div>
    </div>

    <div class="holder">
      <p class="holder-name">Daniel Harwood NZCE (Mech) P&amp;P</p>
      <p class="holder-role">Director</p>
    </div>

    <ul class="contact-list">
      <li>
        <svg class="contact-icon" viewBox="0 0 20 20" aria-hidden="true">
          <circle cx="10" cy="10" r="10" fill="var(--paper)"/>
          <path d="M6.5 5.5 L8.5 5.2 L9.3 7.8 L8.2 8.7 C8.8 10 9.9 11.1 11.2 11.8 L12.2 10.7 L14.8 11.5 L14.5 13.5 C10 13.8 6.2 10 6.5 5.5 Z" fill="var(--leaf-green)"/>
        </svg>
        +614 555 01847
      </li>
      <li>
        <svg class="contact-icon" viewBox="0 0 20 20" aria-hidden="true">
          <circle cx="10" cy="10" r="10" fill="var(--paper)"/>
          <rect x="5" y="6.5" width="10" height="7" fill="none" stroke="var(--leaf-green)" stroke-width="1.4"/>
          <path d="M5 6.5 L10 10.5 L15 6.5" fill="none" stroke="var(--leaf-green)" stroke-width="1.4"/>
        </svg>
        daniel@hexora.co.nz
      </li>
      <li>
        <svg class="contact-icon" viewBox="0 0 20 20" aria-hidden="true">
          <circle cx="10" cy="10" r="10" fill="var(--paper)"/>
          <circle cx="10" cy="10" r="5" fill="none" stroke="var(--leaf-green)" stroke-width="1.3"/>
          <path d="M5 10 H15 M10 5 C7.5 8 7.5 12 10 15 M10 5 C12.5 8 12.5 12 10 15" fill="none" stroke="var(--leaf-green)" stroke-width="1.1"/>
        </svg>
        www.hexora.com.au
      </li>
    </ul>

    <p class="postal">
      Hexora Oil Services 412 Harbour Road<br>
      PO Box 5170 | Eastbank Queensland 4109
    </p>
  </section>

  <section class="card card-back">
    <div class="back-mark">
      <span class="brand-mark-large"></span>
      <span class="brand-word">Hexora</span>
    </div>
    <p class="back-url">www.hexora.com.au</p>
  </section>

</body>
</html>
```